Real Estate Brokerage Stationery Designs

I am looking to have presentation folders with business card slots on both sides along with pockets on both sides. I've attached logos, website colors along with current business card designs.

I am looking for envelope designs both big and small. Possibly new business card designs, notepad templates for big and small notepads. Letterhead designs. Pop socket designs. Realtors name badge designs.

www.brightholdrealty.example

```html
<!DOCTYPE html>
<html lang="en">
<head>
<meta charset="utf-8">
<title>Brighthold Realty – Envelope Set</title>
<link rel="stylesheet" href="https://fonts.googleapis.com/css2?family=Open+Sans:wght@400;600;700&display=swap">
<style>
  :root {
    --backdrop: #a9a9a9;
    --paper: #f4f4f4;
    --paper-shade: #e6e6e6;
    --flap-tone: #b9b9b9;
    --brand-blue: #2e5fb8;
    --accent-blue: #4a8ad8;
    --ink: #2b2b2b;
  }
  * { margin: 0; padding: 0; box-sizing: border-box; }
  html, body { width: 1200px; height: 950px; overflow: hidden; }
  body {
    background: var(--backdrop);
    font-family: "Open Sans", Arial, sans-serif;
    position: relative;
  }
  .envelope {
    position: absolute;
    background: var(--paper);
    box-shadow: 0 6px 14px rgba(0,0,0,0.18);
  }
  .envelope--front {
    left: 70px; top: 110px; width: 600px; height: 260px;
  }
  .envelope__seam {
    position: absolute; left: 270px; bottom: 0; width: 150px; height: 4px;
    background: var(--accent-blue);
  }
  .return-address {
    position: absolute; left: 34px; top: 32px;
  }
  .return-address__brand {
    display: flex; align-items: center; gap: 10px;
  }
  .return-address__mark {
    width: 22px; height: 22px; background: var(--brand-blue);
  }
  .return-address__name {
    font-size: 20px; font-weight: 600; color: var(--ink);
  }
  .return-address__lines {
    margin-top: 8px; font-size: 11px; font-weight: 600; line-height: 1.35;
    color: var(--brand-blue);
  }
  .envelope--back {
    left: 540px; top: 560px; width: 600px; height: 260px;
    background: transparent; box-shadow: none;
  }
  .envelope--back svg { position: absolute; left: 0; top: -150px; overflow: visible; }
  .back-brand {
    position: absolute; right: 70px; bottom: 70px;
    display: flex; align-items: center; gap: 8px;
  }
  .back-brand__mark { width: 16px; height: 16px; background: var(--brand-blue); }
  .back-brand__name { font-size: 15px; font-weight: 600; color: var(--brand-blue); }
</style>
</head>
<body>
  <section class="envelope envelope--front" aria-label="Envelope front">
    <div class="return-address">
      <div class="return-address__brand">
        <span class="return-address__mark"></span>
        <span class="return-address__name">Brighthold Realty</span>
      </div>
      <p class="return-address__lines">2400 Harbor Way, Ste 110,<br>Lakeview, FL 33000</p>
    </div>
    <span class="envelope__seam"></span>
  </section>

  <section class="envelope envelope--back" aria-label="Envelope back with open flap">
    <svg width="600" height="410" viewBox="0 0 600 410">
      <g filter="drop-shadow(0 6px 8px rgba(0,0,0,0.18))">
        <path d="M0 150 L0 135 Q0 115 18 110 L560 20 Q600 10 600 40 L600 410 L0 410 Z" fill="var(--paper)"/>
      </g>
      <path d="M0 150 L0 135 Q0 115 18 110 L560 20 Q600 10 600 40 L600 150 Z"
            fill="var(--flap-tone)" role="img" aria-label="Grey geometric pattern on inner flap"/>
      <path d="M0 150 L600 150 L600 410 L0 410 Z" fill="var(--paper)"/>
      <path d="M0 150 L30 150 Q20 160 20 175 L20 395 Q20 410 40 410" fill="none" stroke="var(--paper-shade)" stroke-width="2"/>
      <path d="M600 150 L560 150 L600 230" fill="none" stroke="var(--paper-shade)" stroke-width="2"/>
    </svg>
    <div class="back-brand">
      <span class="back-brand__mark"></span>
      <span class="back-brand__name">Brighthold Realty</span>
    </div>
  </section>
</body>
</html>
```